RW Holloway LLC Business Card - Civil Engineering & Consulting Firm

We need a Business Card that is elegant, and masculine.  It is our Professional Civil Engineering & Consulting Company located in San Antonio TX (Not s construction or builder firm- no gears & no tool images please). We provide civil engineering services including  commercial site plans, grading and drainage plans, utility plans, hydraulics and hydrology, land planning, utility coordination, and other general civil engineering services related to commercial and residential development.
We have 2 existing Logos. We would like to convey reliability, strength, trustworthiness and attention to detail.  Blues and orange tones as per logo We are OK with the use of a darker blue in the mix.  We have 2 logo versions - Full Company Name Logo to go on the back of card, & Small Icon Logo for the front w/ personal Info.

Target Market(s)
Architects, Real Estate Developers, Other Strctural Engineers, Surveyers, General Contractors
Industry/Entity Type
Professional Civil Engineering
Contact Information for Business Card
Name, Position, Address, Cell & Office #, email, and company website
Font styles to use
Other font styles liked:
- Avian
Requirements
Should not have
- No Tools, No Gears, no Cranes, or Construction Equipment.

```html
<!DOCTYPE html>
<html lang="en">
<head>
<meta charset="utf-8">
<title>RW Holloway LLC – Business Card</title>
<link href="https://fonts.googleapis.com/css2?family=Questrial&family=Arimo:wght@400&display=swap" rel="stylesheet">
<style>
  :root {
    --page-bg: #e9e6e4;
    --frost-light: #f6f1f1;
    --frost-mid: #ede3e3;
    --brand-blue: #78acd8;
    --logo-blue: #6aa2d6;
    --brand-orange: #f0922b;
    --ink-white: #ffffff;
  }
  * { margin: 0; padding: 0; box-sizing: border-box; }
  html, body {
    width: 1200px;
    height: 900px;
    overflow: hidden;
    background: var(--page-bg);
  }
  .business-card {
    position: absolute;
    left: 100px;
    top: 140px;
    width: 1000px;
    height: 619px;
    display: flex;
    box-shadow: 0 10px 30px rgba(0,0,0,0.12);
  }
  .card-brand-side {
    width: 516px;
    height: 100%;
    background: radial-gradient(ellipse at 50% 45%, var(--frost-light) 0%, var(--frost-mid) 100%);
    position: relative;
  }
  .brand-lockup {
    position: absolute;
    left: 60px;
    top: 232px;
    width: 420px;
  }
  .brand-name-row {
    display: flex;
    align-items: center;
    gap: 14px;
  }
  .brand-square {
    width: 26px;
    height: 26px;
    background: var(--logo-blue);
    flex: none;
  }
  .brand-name {
    font-family: "Questrial", sans-serif;
    font-size: 40px;
    letter-spacing: 3px;
    color: var(--logo-blue);
    white-space: nowrap;
  }
  .brand-rule {
    height: 2px;
    background: var(--logo-blue);
    margin: 18px 0 12px 40px;
  }
  .brand-tagline {
    font-family: "Questrial", sans-serif;
    font-size: 16px;
    letter-spacing: 5.6px;
    color: var(--brand-orange);
    margin-left: 40px;
    white-space: nowrap;
  }
  .card-divider {
    width: 11px;
    height: 100%;
    background: var(--brand-orange);
  }
  .card-contact-side {
    flex: 1;
    height: 100%;
    background: var(--brand-blue);
    color: var(--ink-white);
    padding: 158px 0 0 46px;
  }
  .person-name {
    font-family: "Questrial", sans-serif;
    font-size: 40px;
    line-height: 42px;
    letter-spacing: 0.5px;
  }
  .person-title {
    font-family: "Arimo", sans-serif;
    font-size: 25px;
    line-height: 30px;
    margin-top: 2px;
  }
  .contact-list {
    list-style: none;
    margin-top: 20px;
    font-family: "Arimo", sans-serif;
    font-size: 27px;
    line-height: 36.5px;
  }
  .contact-item {
    display: flex;
    align-items: center;
    gap: 9px;
  }
  .contact-icon {
    width: 26px;
    height: 26px;
    flex: none;
  }
  .postal-address {
    font-family: "Arimo", sans-serif;
    font-style: normal;
    font-size: 27px;
    line-height: 37px;
    margin-top: 20px;
  }
</style>
</head>
<body>
  <div class="business-card">
    <section class="card-brand-side">
      <div class="brand-lockup">
        <div class="brand-name-row">
          <span class="brand-square"></span>
          <span class="brand-name">RW HOLLOWAY LLC</span>
        </div>
        <div class="brand-rule"></div>
        <div class="brand-tagline">CONSULTING ENGINEERS</div>
      </div>
    </section>
    <div class="card-divider"></div>
    <section class="card-contact-side">
      <h1 class="person-name">DANIEL MERCER</h1>
      <p class="person-title">MANAGING DIRECTOR</p>
      <ul class="contact-list">
        <li class="contact-item">
          <svg class="contact-icon" viewBox="0 0 24 24" aria-hidden="true">
            <path fill="#fff" d="M6.6 10.8c1.4 2.8 3.8 5.1 6.6 6.6l2.2-2.2c.3-.3.7-.4 1-.2 1.1.4 2.3.6 3.6.6.6 0 1 .4 1 1V20c0 .6-.4 1-1 1C10.6 21 3 13.4 3 4c0-.6.4-1 1-1h3.5c.6 0 1 .4 1 1 0 1.3.2 2.5.6 3.6.1.3 0 .7-.2 1z"/>
            <path fill="none" stroke="#fff" stroke-width="1.6" d="M14 3.5a7 7 0 0 1 6.5 6.5M14 7a3.5 3.5 0 0 1 3 3"/>
          </svg>
          <span>044-123 456 789</span>
        </li>
        <li class="contact-item">
          <svg class="contact-icon" viewBox="0 0 24 24" aria-hidden="true">
            <rect x="2" y="5" width="20" height="14" fill="#fff"/>
            <path d="M2 5l10 8 10-8M2 19l7.5-7M22 19l-7.5-7" fill="none" stroke="#78acd8" stroke-width="1.4"/>
          </svg>
          <span>info@webname.com</span>
        </li>
        <li class="contact-item">
          <svg class="contact-icon" viewBox="0 0 24 24" aria-hidden="true">
            <g fill="none" stroke="#fff" stroke-width="1.7">
              <circle cx="12" cy="12" r="10"/>
              <ellipse cx="12" cy="12" rx="4.5" ry="10"/>
              <path d="M2 12h20M3.5 7h17M3.5 17h17"/>
            </g>
          </svg>
          <span>www.websitename.com</span>
        </li>
      </ul>
      <address class="postal-address">
        421, Address line goes here<br>
        45452,Country Name
      </address>
    </section>
  </div>
</body>
</html>
```